Flat Belly Design Graphics for Social

I want to create 9 social media graphics (new Instagram size 4:5 (1080 x 1350 pixels) focusing on our Flat Belly Graphics, using the pics attached. Use the attached pics, NO RANDOM STOCK PHOTOGRAPHY. For the color scheme of the graphics, the color palette is attached. YOU MUST POST ALL 9 GRAPHICS IN ONE ENTRY.
Using the 3 titles below, create one set of graphics. 1) with all text, then for the others, use the pictures as detailed below in IMPORTANT:
1. Ten-Week Bright Morning Reboot
2. The Quick Garden Kitchen Menu Guide
3. Studio Habits for Lasting Energy Past Midlife - Zero Gym Needed
IMPORTANT:
Only use RK Pic 1 and RK Pic 2 with the title, Ten-Week Bright Morning Reboot
Only use meal plan1 and meal plan2 pics with the title, Quick Garden Kitchen Menu Guide
Only use studio habits 1 and studio habits 2 pics with the title, Studio Habits for Lasting Energy Past Midlife - Zero Gym Needed
women over 40

```html
<!DOCTYPE html>
<html lang="en">
<head>
<meta charset="utf-8">
<title>Social Graphics Set</title>
<link href="https://fonts.googleapis.com/css2?family=Bebas+Neue&display=swap" rel="stylesheet">
<style>
:root{
  --backdrop:#1e0008;
  --forest:#2f4b48;
  --berry:#b44f6c;
  --blush:#fbeeee;
  --rose:#e397ab;
  --white:#ffffff;
}
*{margin:0;padding:0;box-sizing:border-box}
html,body{width:1075px;height:1200px;overflow:hidden;background:var(--backdrop)}
body{position:relative;font-family:"Bebas Neue",Impact,sans-serif}
.card{position:absolute;width:217px;height:271px;overflow:hidden}
.card svg.shapes{position:absolute;inset:0;width:100%;height:100%}
.title-box{position:absolute;left:20px;top:21px;width:169px;height:218px;background:var(--white);border-radius:12px;box-shadow:0 3px 4px rgba(0,0,0,.18);display:flex;flex-direction:column;align-items:center;justify-content:center;text-align:center}
.line{display:block;line-height:.92;white-space:nowrap}
.green{color:var(--forest)}
.berry{color:var(--berry)}
.white{color:var(--white)}
.rosetext{color:var(--rose)}
.pill{position:absolute;left:25px;top:6px;width:166px;height:259px;border-radius:83px}
.pill.rose{background:var(--rose)}
.pill.forest{background:var(--forest)}
.portrait{position:absolute;left:44px;top:15px;width:129px;height:129px;border-radius:50%}
.pill-text{position:absolute;left:25px;width:166px;top:150px;height:105px;display:flex;flex-direction:column;align-items:center;justify-content:center;text-align:center}
.italic{font-style:italic}
.photo{position:absolute;inset:0}
.band-text{position:absolute;left:0;right:0;top:158px;bottom:6px;display:flex;flex-direction:column;align-items:center;justify-content:center;text-align:center}
.tag{background:var(--rose);color:var(--white);padding:1px 7px 0;margin-top:3px}
.shadowed{text-shadow:0 2px 3px rgba(0,0,0,.35)}
.person-tone{background:radial-gradient(circle at 50% 40%,#efe7e4 0%,#b99a86 45%,#6e5546 100%)}
.food-tone{background:radial-gradient(circle at 50% 50%,#e9e2d6 0%,#8a6b4c 40%,#4b3426 75%,#5c7a3a 100%)}
.friends-tone{background:radial-gradient(circle at 50% 45%,#d8b39d 0%,#9c7460 45%,#e8e0dc 100%)}
.friends-sky{background:linear-gradient(160deg,#7ccde0 0%,#5ab9d2 100%)}
</style>
</head>
<body>

<!-- Row one: text-only titles -->
<section class="card" style="left:197px;top:177px">
  <svg class="shapes" viewBox="0 0 217 271"><rect width="217" height="271" fill="var(--blush)"/><polygon points="0,0 91,0 0,109" fill="var(--forest)"/><polygon points="217,171 217,271 120,271" fill="var(--berry)"/></svg>
  <div class="title-box">
    <span class="line green" style="font-size:42px">Ten-Week</span>
    <span class="line berry" style="font-size:60px">Bright</span>
    <span class="line berry" style="font-size:50px">Morning</span>
    <span class="line green" style="font-size:38px">Reboot</span>
  </div>
</section>

<section class="card" style="left:431px;top:177px">
  <svg class="shapes" viewBox="0 0 217 271"><rect width="217" height="271" fill="var(--blush)"/><polygon points="0,0 91,0 0,109" fill="var(--forest)"/><polygon points="217,171 217,271 120,271" fill="var(--berry)"/></svg>
  <div class="title-box">
    <span class="line green" style="font-size:28px">The Quick</span>
    <span class="line berry" style="font-size:58px">Garden</span>
    <span class="line berry" style="font-size:50px">Kitchen</span>
    <span class="line green" style="font-size:36px">Menu Guide</span>
  </div>
</section>

<section class="card" style="left:662px;top:177px">
  <svg class="shapes" viewBox="0 0 217 271"><rect width="217" height="271" fill="var(--white)"/><polygon points="0,0 91,0 0,109" fill="var(--forest)"/><polygon points="217,171 217,271 120,271" fill="var(--berry)"/></svg>
  <div class="title-box">
    <span class="line green" style="font-size:34px">Studio Habits</span>
    <span class="line green" style="font-size:34px">For Lasting</span>
    <span class="line berry" style="font-size:34px">Energy Past</span>
    <span class="line berry" style="font-size:50px">Midlife</span>
    <span class="line green" style="font-size:22px;margin-top:3px">Zero Gym Needed</span>
  </div>
</section>

<!-- Row two: arched frames with round photos -->
<section class="card" style="left:197px;top:464px;background:var(--blush)">
  <div class="pill rose"></div>
  <div class="portrait person-tone" role="img" aria-label="Smiling woman in a white cropped sweater pointing at her waist in a kitchen"></div>
  <div class="pill-text">
    <span class="line green" style="font-size:32px">Ten-Week</span>
    <span class="line green" style="font-size:28px">Bright Morning</span>
    <span class="line white" style="font-size:24px">Reboot</span>
  </div>
</section>

<section class="card" style="left:431px;top:464px;background:var(--forest)">
  <div class="pill rose"></div>
  <div class="portrait food-tone" role="img" aria-label="Meal plan notepad surrounded by fresh fruit, vegetables and chicken on a wooden table"></div>
  <div class="pill-text">
    <span class="line green italic" style="font-size:28px">The Quick Garden</span>
    <span class="line green italic" style="font-size:28px">Kitchen Menu</span>
    <span class="line white" style="font-size:24px">Guide</span>
  </div>
</section>

<section class="card" style="left:662px;top:464px;background:var(--rose)">
  <div class="pill forest"></div>
  <div class="portrait friends-tone" role="img" aria-label="Woman whispering a secret to a surprised friend"></div>
  <div class="pill-text">
    <span class="line white" style="font-size:19px">Studio Habits For</span>
    <span class="line white" style="font-size:19px">Lasting Energy Past Midlife</span>
    <span class="line rosetext" style="font-size:16px;margin-top:4px">Zero Gym Needed</span>
  </div>
</section>

<!-- Row three: full photos with curved bands -->
<section class="card" style="left:197px;top:752px">
  <div class="photo person-tone" role="img" aria-label="Smiling woman in a white cropped sweater pointing at her waist in a kitchen"></div>
  <svg class="shapes" viewBox="0 0 217 271"><path d="M0,172 Q108,128 217,172 L217,271 L0,271 Z" fill="var(--forest)"/></svg>
  <div class="band-text">
    <span class="line white shadowed" style="font-size:40px">Ten-Week</span>
    <span class="line white shadowed" style="font-size:34px">Bright Morning</span>
    <span class="line rosetext" style="font-size:24px">Reboot</span>
  </div>
</section>

<section class="card" style="left:428px;top:752px">
  <div class="photo food-tone" role="img" aria-label="Meal plan sheet with chicken, berries, asparagus, potatoes and grains on a wooden table"></div>
  <svg class="shapes" viewBox="0 0 217 271"><path d="M0,162 Q108,120 217,162 L217,271 L0,271 Z" fill="var(--rose)"/></svg>
  <div class="band-text">
    <span class="line green" style="font-size:32px">The Quick Garden</span>
    <span class="line green" style="font-size:32px">Kitchen Menu</span>
    <span class="line white" style="font-size:24px;margin-top:4px">Guide</span>
  </div>
</section>

<section class="card" style="left:662px;top:752px">
  <div class="photo friends-sky" role="img" aria-label="Woman whispering a secret to a surprised friend against a blue backdrop"></div>
  <svg class="shapes" viewBox="0 0 217 271"><path d="M0,165 Q108,125 217,165 L217,271 L0,271 Z" fill="var(--forest)"/></svg>
  <div class="band-text">
    <span class="line white" style="font-size:23px">Studio Habits For</span>
    <span class="line white" style="font-size:23px">Lasting Energy</span>
    <span class="line white" style="font-size:23px">Past Midlife</span>
    <span class="line tag" style="font-size:22px">Zero Gym Needed</span>
  </div>
</section>

</body>
</html>
```